Window Treatment business needs website redesigned.

We need a revamp and refresh of our current site www.velmarix.ca
Looking to attract very high end customer. It should be a very simple design with very little text. This site will be visited by prospective homeowners, designers, builders and architects. They should feel that they are dealing with a high-end product selection, where experience, customer service and unique product offering is the focus. The content will be to highlight our services and highlight the manufacturers we sell, using a few rich photos to highlight the products. We should NOT look like we are a very large company. It should NOT have discounts/savings buttons and many menus to choose from. We offer over 15 years experience to narrow the many market options, to provide the right technical solution.
We specialize in products that are not readily available on the market and specifically motorized systems for indoors and outdoors.
Our main suppliers are Kravenholt.com, Dimbrell.com
We carry our own locally manufactured product line of roller shades.
Main product pictures should be of roller shades, outdoor bug screens, awnings and outdoor pergolas.

Reason: I understand that Christmas is coming up real short and many people are extremely busy. If you have a CREATIVE gifting you still want to submit, I look forward to your idea!

Reason: Due to holiday season, we have not had sufficient time to review to make a final decision. Thank you for your patience!

Target Market(s)

High end home owners, designers, builders, architects

Industry/Entity Type

Contractor

Coding

Coded - Design and coding required

Number of Pages Required

3 page

Font styles to use
Sans Serif

Requirements
Must have
• Landing page with full size image like homepage of zolvane.it
• Products page that highlights products with simple product shot image, description and link to manufacturer.
• On main page a scrolling of customer reviews.
• I want a very simple, eye-catching, emotional image for homepage. It does not need to include any product image.
• An image that shows technology combining/meshing with hand craftsmanship.
• Focus is on design.
• http://www.zolvane.it/en/gallery is a great layout and design.
Nice to have
• Logo shape for icons and watermark should be used.
• Look like and have simple motion effects like quorix.com or telvarin.com
Should not have
• Generic/standard looking feel like bluppet.com or mecklorwindow.ca
• No use of green as background only subtle text.
• Lots of text and pages.

```html
<!DOCTYPE html>
<html lang="en">
<head>
<meta charset="utf-8">
<title>Velmarix — Mediaroom</title>
<link rel="stylesheet" href="https://fonts.googleapis.com/css2?family=Open+Sans:wght@300;400;600;700&display=swap">
<style>
:root{
  --page:#eeeeee;
  --panel:#ffffff;
  --ink:#3b3b3b;
  --muted:#8a8a8a;
  --green:#6cb33f;
  --white:#ffffff;
}
*{box-sizing:border-box;margin:0;padding:0}
html,body{width:764px;height:1200px;overflow:hidden}
body{position:relative;background:var(--page);font-family:"Open Sans",sans-serif;color:var(--ink)}
.hero{position:absolute;left:0;top:0;width:764px;height:424px;
  background:linear-gradient(160deg,#5a4a3a 0%,#8a6d4e 35%,#c9a57a 55%,#6b5544 80%,#3d3128 100%)}
.hero-frame{position:absolute;left:26px;top:52px;right:26px;bottom:0;border:1px solid rgba(255,255,255,.55);border-bottom:none}
.menu-toggle{position:absolute;left:0;top:20px;width:30px;height:26px;background:var(--green);display:flex;flex-direction:column;justify-content:center;align-items:center;gap:4px}
.menu-toggle span{display:block;width:14px;height:2px;background:var(--white)}
.brand{position:absolute;left:112px;top:12px;display:flex;align-items:center;gap:8px}
.brand-mark{width:26px;height:26px;border-radius:50%;background:var(--white)}
.brand-name{font-size:20px;font-weight:600;color:var(--white);letter-spacing:.5px}
.hero-title{position:absolute;left:0;right:0;top:252px;text-align:center;color:var(--white)}
.hero-title h1{font-size:36px;font-weight:700;line-height:1}
.hero-title p{font-size:17px;font-weight:300;margin-top:4px}

.content{position:absolute;left:90px;top:424px;width:584px;height:752px;background:var(--panel);padding:46px 12px 0}
.row{display:flex;height:172px}
.row.reverse{flex-direction:row-reverse}
.media{position:relative;width:280px;height:172px;flex:none;overflow:hidden}
.photo-family{background:linear-gradient(135deg,#6b5a4a,#b59a7e 50%,#4c3d33)}
.photo-garden{background:linear-gradient(180deg,#7c8a86,#4f5f4a 55%,#2e3529)}
.photo-hands{background:linear-gradient(135deg,#d8dde3,#9aa7b5 50%,#e9ecef)}
.photo-jars{background:linear-gradient(135deg,#9fa3a0,#d9d8cf 50%,#5f625e)}
.player-top{position:absolute;left:0;right:0;top:0;height:16px;background:rgba(0,0,0,.55)}
.player-bar{position:absolute;left:0;right:0;bottom:0;height:18px;background:rgba(0,0,0,.75);display:flex;align-items:center;padding:0 6px;gap:6px}
.progress{flex:1;height:3px;background:rgba(255,255,255,.35)}

.entry{width:280px;padding:0 20px;display:flex;flex-direction:column;justify-content:center;text-align:center}
.entry h2{font-size:19px;font-weight:400;color:var(--ink);line-height:1.2}
.entry h2 em{font-style:normal;color:var(--green)}
.meta{font-size:6.5px;color:var(--muted);margin:6px 0 8px;display:flex;justify-content:center;align-items:center;gap:4px}
.entry p{font-size:7px;line-height:1.55;color:var(--muted);text-align:left}
.footer{position:absolute;left:0;right:0;top:1184px;text-align:center;font-size:6.5px;color:var(--muted)}
</style>
</head>
<body>
<header class="hero" role="img" aria-label="Warm modern kitchen and dining interior seen through large open glass doors at dusk">
  <div class="hero-frame"></div>
  <div class="menu-toggle"><span></span><span></span><span></span></div>
  <div class="brand"><span class="brand-mark"></span><span class="brand-name">Velmarix</span></div>
  <div class="hero-title"><h1>Mediaroom</h1><p>articles &amp; videos</p></div>
</header>

<main class="content">
  <section class="row">
    <div class="media photo-family" role="img" aria-label="Mother holding two young children in a bright living room"></div>
    <article class="entry">
      <h2>Article <em>Title</em></h2>
      <div class="meta"><svg width="7" height="7" viewBox="0 0 10 10"><rect x="1" y="2" width="8" height="7" fill="none" stroke="#8a8a8a"/></svg>January · 16 · 2017</div>
      <p>Our team visits every home to measure, advise and fit motorized shades with care. Each project blends quiet technology with skilled hands, giving owners, designers and builders a calm result that lasts for many seasons ahead.</p>
    </article>
  </section>

  <section class="row reverse">
    <div class="media photo-garden" role="img" aria-label="Video still of a person walking along a leafy garden path">
      <div class="player-top"></div>
      <div class="player-bar"><svg width="7" height="8" viewBox="0 0 7 8"><path d="M0 0L7 4L0 8Z" fill="#fff"/></svg><div class="progress"></div></div>
    </div>
    <article class="entry">
      <h2>Video <em>Title</em></h2>
      <div class="meta"><svg width="7" height="7" viewBox="0 0 10 10"><rect x="1" y="2" width="8" height="7" fill="none" stroke="#8a8a8a"/></svg>January · 16 · 2017</div>
      <p>Our team visits every home to measure, advise and fit motorized shades with care. Each project blends quiet technology with skilled hands, giving owners, designers and builders a calm result that lasts for many seasons ahead.</p>
    </article>
  </section>

  <section class="row">
    <div class="media photo-hands" role="img" aria-label="Video still of hands holding a small glass bottle">
      <div class="player-bar"><svg width="7" height="8" viewBox="0 0 7 8"><path d="M0 0L7 4L0 8Z" fill="#fff"/></svg><div class="progress"></div></div>
    </div>
    <article class="entry">
      <h2>Video <em>Title</em></h2>
      <div class="meta"><svg width="7" height="7" viewBox="0 0 10 10"><rect x="1" y="2" width="8" height="7" fill="none" stroke="#8a8a8a"/></svg>January · 16 · 2017</div>
      <p>Our team visits every home to measure, advise and fit motorized shades with care. Each project blends quiet technology with skilled hands, giving owners, designers and builders a calm result that lasts for many seasons ahead.</p>
    </article>
  </section>

  <section class="row reverse">
    <div class="media photo-jars" role="img" aria-label="Close view of labelled tin jars on a table"></div>
    <article class="entry">
      <h2>Article <em>Title</em></h2>
      <div class="meta"><svg width="7" height="7" viewBox="0 0 10 10"><rect x="1" y="2" width="8" height="7" fill="none" stroke="#8a8a8a"/></svg>January · 16 · 2017</div>
      <p>Our team visits every home to measure, advise and fit motorized shades with care. Each project blends quiet technology with skilled hands, giving owners, designers and builders a calm result that lasts for many seasons ahead.</p>
    </article>
  </section>
</main>

<footer class="footer">Copyright © 2016 Velmarix Inc. All Rights Reserved</footer>
</body>
</html>
```